Personal letterhead and stationary

I am looking for someone to design letterhead and stationary set for my personal use. I want something simple and timeless with a little bit of color. I like photography, computers and writing.

```html
<!DOCTYPE html>
<html lang="en">
<head>
<meta charset="utf-8">
<title>Daniel Roy Carter — Letterhead</title>
<link href="https://fonts.googleapis.com/css2?family=Josefin+Slab:wght@400;600&display=swap" rel="stylesheet">
<style>
  :root {
    --ink: #1a1a1a;
    --rule: #8a8a8a;
    --paper: #ffffff;
    --backdrop: #ffffff;
  }
  html, body {
    margin: 0;
    padding: 0;
    overflow: hidden;
    background: var(--backdrop);
  }
  .letterhead {
    position: relative;
    width: 865px;
    height: 1200px;
    background: var(--paper);
    color: var(--ink);
    font-family: "Josefin Slab", Georgia, serif;
    overflow: hidden;
  }
  .top-edge {
    position: absolute;
    left: 0; right: 0; top: 12px;
    border-top: 1px solid #d6d6d6;
  }
  .header-rule {
    position: absolute;
    top: 118px;
    height: 3px;
    border-top: 1px solid var(--ink);
    border-bottom: 1px solid var(--ink);
  }
  .header-rule.left { left: 62px; width: 300px; }
  .header-rule.right { left: 503px; width: 312px; }
  .name {
    position: absolute;
    left: 86px; top: 90px;
    margin: 0;
    font-size: 24px;
    font-weight: 400;
    letter-spacing: 0.5px;
    line-height: 1;
    white-space: nowrap;
    text-transform: uppercase;
  }
  .email {
    position: absolute;
    left: 86px; top: 130px;
    font-size: 15px;
  }
  .wordmark {
    position: absolute;
    left: 368px; top: 100px;
    width: 128px;
    text-align: center;
    font-size: 30px;
    font-weight: 400;
    letter-spacing: 3px;
    line-height: 1;
  }
  .phone {
    position: absolute;
    left: 664px; top: 88px;
    display: flex;
    align-items: center;
    gap: 6px;
    font-size: 20px;
    line-height: 1;
  }
  .phone svg { width: 18px; height: 18px; fill: var(--ink); }
  .address {
    position: absolute;
    right: 52px; top: 130px;
    font-size: 15px;
  }
  .footer-rule {
    position: absolute;
    left: 62px; right: 50px; top: 1128px;
    border-top: 1px solid var(--rule);
  }
  .motto {
    position: absolute;
    left: 0; right: 0; top: 1136px;
    text-align: center;
    font-size: 13px;
    line-height: 1.35;
    letter-spacing: 0.5px;
  }
  .motto p { margin: 0; }
</style>
</head>
<body>
<main class="letterhead">
  <div class="top-edge"></div>

  <h1 class="name">Daniel Roy Carter</h1>
  <div class="header-rule left"></div>
  <div class="email">daniel@carterpost.com.au</div>

  <div class="wordmark">DRC</div>

  <div class="phone">
    <svg viewBox="0 0 24 24" aria-hidden="true"><path d="M6.6 10.8c1.4 2.8 3.8 5.1 6.6 6.6l2.2-2.2c.3-.3.7-.4 1-.2 1.1.4 2.300.6 3.6.6.6 0 1 .4 1 1V20c0 .6-.4 1-1 1C10.6 21 3 13.4 3 4c0-.6.4-1 1-1h3.5c.6 0 1 .4 1 1 0 1.3.2 2.5.6 3.6.1.3 0 .7-.2 1l-2.3 2.2z"/></svg>
    <span>0400 555 182</span>
  </div>
  <div class="header-rule right"></div>
  <div class="address">14 linden st bendale vic 3621</div>

  <div class="footer-rule"></div>
  <footer class="motto">
    <p>Be the change you want to see in the World</p>
    <p>-Arun Vale</p>
  </footer>
</main>
</body>
</html>
```